Hello my Name is Elias Moreno. I buy and sell vintage comic books, you can refer to my instragram page qpkz.comics to get ideas and inspiration. For the front of the card I would like my company logo QPKZ Comics with a yellow and black background with the bat signal or bat emblem like on my IG page and with my info Elias Moreno as the Owner and address/ phone number, PO Box 617283, Miami, FL 33827, 305-482-6170 and that I buy and sell comics & collectables . Also feel free to be open to other ideas if you want. Im not stuck on one design. For the back of the card I would like for it to say follow me on Instagram QPKZ.Comics with the ig emblem. Also would like the card to be vertical if possible. Thanks

```html
<!DOCTYPE html>
<html lang="en">
<head>
<meta charset="utf-8">
<title>QPKZ Comics – Business Card</title>
<link rel="stylesheet" href="https://fonts.googleapis.com/css2?family=Open+Sans:wght@400;600;700&display=swap">
<style>
  :root {
    --page-bg: #e9e7e3;
    --card-white: #ffffff;
    --card-dark: #2b2b2b;
    --brand-yellow: #f7c21b;
    --ink-black: #111111;
    --ink-grey: #3a3a3a;
    --text-light: #ffffff;
  }
  * { box-sizing: border-box; margin: 0; padding: 0; }
  html, body {
    width: 1200px; height: 900px; overflow: hidden;
    background: var(--page-bg);
    font-family: "Open Sans", Arial, sans-serif;
  }
  .stage {
    position: relative; width: 1200px; height: 900px;
  }
  .card {
    position: absolute; left: 280px;
    width: 640px; height: 366px;
    overflow: hidden;
    box-shadow: 0 6px 18px rgba(0,0,0,0.18);
  }
  .card--back { top: 64px; background: var(--card-dark); }
  .card--front { top: 470px; background: var(--card-white); }

  .card-shapes { position: absolute; inset: 0; width: 100%; height: 100%; }

  /* brand mark: name plus one plain circle */
  .brand {
    position: absolute; display: flex; align-items: center; gap: 14px;
  }
  .brand-dot { width: 46px; height: 46px; border-radius: 50%; flex: none; }
  .brand-name { font-weight: 700; font-size: 34px; letter-spacing: 0.5px; white-space: nowrap; }
  .card--back .brand { left: 300px; top: 110px; }
  .card--back .brand-dot { background: var(--text-light); }
  .card--back .brand-name { color: var(--text-light); }
  .card--front .brand { left: 330px; top: 150px; }
  .card--front .brand-dot { background: var(--brand-yellow); }
  .card--front .brand-name { color: var(--brand-yellow); }

  /* back */
  .follow {
    position: absolute; left: 120px; top: 236px;
    display: flex; align-items: center; gap: 14px;
    color: var(--text-light);
  }
  .follow-label { font-weight: 700; font-size: 17px; text-transform: uppercase; }
  .follow-dot { width: 30px; height: 30px; border-radius: 50%; background: var(--brand-yellow); }
  .follow-handle { font-weight: 600; font-size: 22px; }

  /* front */
  .owner { position: absolute; left: 86px; top: 34px; }
  .owner-name {
    color: var(--brand-yellow); font-weight: 700; font-size: 22px;
    text-transform: uppercase; line-height: 1.1;
  }
  .owner-role { color: var(--ink-grey); font-size: 14px; }

  .contact { position: absolute; left: 44px; top: 168px; color: var(--ink-grey); font-size: 17px; line-height: 1.35; }
  .contact-row { display: flex; align-items: flex-start; gap: 8px; }
  .contact-row svg { flex: none; margin-top: 4px; }
  .contact-indent { padding-left: 22px; }

  .tagline {
    position: absolute; right: 40px; top: 232px;
    text-align: right; color: var(--brand-yellow);
    font-weight: 700; font-size: 18px; line-height: 1.2; text-transform: uppercase;
  }
</style>
</head>
<body>
<main class="stage">

  <section class="card card--back" aria-label="Card back">
    <div class="brand">
      <span class="brand-dot"></span>
      <span class="brand-name">QPKZ Comics</span>
    </div>
    <div class="follow">
      <span class="follow-label">Follow me on</span>
      <span class="follow-dot"></span>
      <span class="follow-handle">QPKZ.Comics</span>
    </div>
  </section>

  <section class="card card--front" aria-label="Card front">
    <svg class="card-shapes" viewBox="0 0 640 366" aria-hidden="true">
      <polygon points="0,24 40,24 28,50 0,50" fill="var(--brand-yellow)"/>
      <polygon points="36,30 62,30 50,56 18,56" fill="var(--ink-black)"/>
      <polygon points="0,296 310,296 296,316 0,316" fill="var(--brand-yellow)"/>
      <polygon points="318,316 640,316 640,366 290,366" fill="var(--ink-black)"/>
    </svg>

    <div class="owner">
      <p class="owner-name">Elias Moreno</p>
      <p class="owner-role">Owner</p>
    </div>

    <div class="contact">
      <p class="contact-row">
        <svg width="14" height="14" viewBox="0 0 24 24"><path fill="var(--brand-yellow)" d="M6.6 10.8a15.1 15.1 0 0 0 6.6 6.6l2.2-2.2a1 1 0 0 1 1-.25 11.4 11.4 0 0 0 3.6.57 1 1 0 0 1 1 1V20a1 1 0 0 1-1 1A17 17 0 0 1 3 4a1 1 0 0 1 1-1h3.5a1 1 0 0 1 1 1c0 1.25.2 2.45.57 3.57a1 1 0 0 1-.25 1z"/></svg>
        <span>305-482-6170</span>
      </p>
      <p class="contact-row">
        <svg width="14" height="16" viewBox="0 0 24 28"><path fill="var(--brand-yellow)" d="M12 0a10 10 0 0 0-10 10c0 7.5 10 18 10 18s10-10.5 10-18A10 10 0 0 0 12 0zm0 14a4 4 0 1 1 0-8 4 4 0 0 1 0 8z"/></svg>
        <span>PO Box 617283,</span>
      </p>
      <p class="contact-indent">Miami, FL 33827</p>
    </div>

    <div class="brand">
      <span class="brand-dot"></span>
      <span class="brand-name">QPKZ Comics</span>
    </div>

    <p class="tagline">We buy and sell comics<br>&amp; collectables</p>
  </section>

</main>
</body>
</html>
```